Restaurant Digital TV Menu Pictures

Need a digital menu board, image square of food. Something simple for customer to look and point to or say the food number. Image square 4x6, 5x7 or various of that. Vietnamese restaurant type food. I need template created and designer choice of design. Color scheme orange and white and little green. I would like to in the title of the food myself and written detail myself. I just need the template and possible have the design edit the picture a bit. Total food about 30 image will mostly be about 20-30 images. This will be display on a TV screen 16:9 size on a 55 inch tv. Attached is the food menu item. Also attach how the image off food will be taken. Also attach of other people design on the web. However, I would like number be label on the food item. I can find tune the correct information and food type and numbers later.

Font styles to use
Decorative

Colors
f37122
fffefb
9bcb3c

Requirements
Must have
• Photo edit food image basic making it pop. Make it look better, not magic, but better than my photography. Asian feel to the design.
Nice to have
• Fresh image of ingredients, (cilantro, freshly cook, non fast food) Image of green food

```html
<!DOCTYPE html>
<html lang="en">
<head>
<meta charset="utf-8">
<title>Beef Rice – Menu Board Cards</title>
<link rel="stylesheet" href="https://fonts.googleapis.com/css2?family=Anton&family=Open+Sans:wght@400&family=Montserrat:wght@700&display=swap">
<style>
  :root {
    --orange: #f37122;
    --orange-light: #f58c4f;
    --cream: #fffefb;
    --green: #9bcb3c;
    --backdrop: #3d3d3d;
    --ink: #222222;
    --shadow: #5a2a10;
    --plate: #1c1c1c;
    --plate-food: #4a3424;
  }
  html, body {
    margin: 0;
    padding: 0;
    width: 1200px;
    height: 654px;
    overflow: hidden;
    background: #ffffff;
  }
  .stage {
    position: relative;
    width: 1200px;
    height: 654px;
    overflow: hidden;
  }
  .board {
    position: absolute;
    left: 0;
    top: 0;
    width: 2560px;
    height: 1395px;
    transform: scale(0.46875);
    transform-origin: 0 0;
  }
  .backdrop {
    position: absolute;
    left: 0;
    top: 0;
    width: 2075px;
    height: 1395px;
    background: var(--backdrop);
  }
  .card {
    position: absolute;
    left: var(--x);
    top: var(--y);
    width: 500px;
    height: 263px;
    background: var(--cream);
    overflow: hidden;
  }
  .card-head {
    position: absolute;
    left: 0;
    top: 0;
    width: 100%;
    height: 38px;
    background: linear-gradient(var(--orange) 0 64%, var(--orange-light) 64% 100%);
  }
  .card-title {
    position: absolute;
    left: 0;
    top: -4px;
    width: 100%;
    margin: 0;
    text-align: center;
    font-family: "Anton", sans-serif;
    font-weight: 400;
    font-size: 30px;
    line-height: 40px;
    letter-spacing: 1px;
    color: var(--cream);
    text-shadow: 2px 2px 0 var(--shadow);
  }
  .card-desc {
    position: absolute;
    left: 30px;
    top: 54px;
    width: 152px;
    margin: 0;
    font-family: "Open Sans", sans-serif;
    font-size: 8.3px;
    line-height: 10.5px;
    color: var(--ink);
  }
  .card-price {
    position: absolute;
    left: 36px;
    top: 134px;
    margin: 0;
    font-family: "Anton", sans-serif;
    font-size: 46px;
    line-height: 56px;
    color: var(--orange);
    -webkit-text-stroke: 1.5px var(--cream);
    text-shadow: 2px 2px 0 var(--shadow);
  }
  .order-tag {
    position: absolute;
    left: 35px;
    top: 205px;
    width: 126px;
    height: 23px;
    background: var(--green);
    clip-path: polygon(0 0, 88% 0, 100% 100%, 0 100%);
    display: flex;
    align-items: center;
    gap: 4px;
    padding-left: 10px;
    box-sizing: border-box;
    font-family: "Montserrat", sans-serif;
    font-weight: 700;
    font-size: 13.5px;
    color: var(--cream);
    text-shadow: 1px 1px 0 #2c4a10;
  }
  .order-icon { width: 11px; height: 11px; flex: none; }
  .halo {
    position: absolute;
    left: 190px;
    top: 30px;
    width: 230px;
    height: 250px;
    border-radius: 50%;
    background: radial-gradient(circle, #eeeeee 0 35%, transparent 70%);
    opacity: 0.6;
  }
  .dish-photo {
    position: absolute;
    left: 256px;
    top: 46px;
    width: 226px;
    height: 226px;
    border-radius: 50%;
    box-sizing: border-box;
    border: 4px solid var(--green);
    box-shadow: inset 0 0 0 4px var(--orange);
    background: radial-gradient(circle, var(--plate-food) 0%, #33261c 55%, var(--plate) 85%);
  }
  .rule { position: absolute; }
  .rule-green-v { left: 13px; top: 95px; width: 2px; height: 168px; background: var(--green); }
  .rule-orange-v { left: 19px; top: 160px; width: 2px; height: 103px; background: var(--orange); }
  .rule-orange-h { left: 0; top: 257px; width: 180px; height: 2px; background: var(--orange); }
  .rule-green-h { left: 180px; top: 259px; width: 70px; height: 2px; background: var(--green); }
</style>
</head>
<body>
<svg width="0" height="0" style="position:absolute">
  <defs>
    <symbol id="tap" viewBox="0 0 12 12">
      <circle cx="6" cy="6" r="5.5" fill="#fffefb"/>
      <rect x="5" y="2.5" width="2" height="6" rx="1" fill="#1f1f1f"/>
      <rect x="4" y="6" width="4" height="3.5" rx="1.2" fill="#1f1f1f"/>
    </symbol>
  </defs>
</svg>
<div class="stage">
<main class="board">
  <div class="backdrop"></div>

  <article class="card" style="--x:0px;--y:0px"><div class="card-head"></div><h2 class="card-title">BEEF RICE</h2><p class="card-desc">Lorem ipsum dolor sit amet, consectetur adipiscing elit, sed do eiusmod tempor incididunt ut labore et dolore magna aliqua. Ut enim ad minim veniam, quis ostrud itation ullamco</p><div class="halo"></div><div class="dish-photo" role="img" aria-label="Beef rice bowl with grilled beef, slaw, spring roll and dipping sauce"></div><p class="card-price">$9.99</p><div class="order-tag"><svg class="order-icon"><use href="#tap"/></svg>ORDER NOW</div><span class="rule rule-green-v"></span><span class="rule rule-orange-v"></span><span class="rule rule-orange-h"></span><span class="rule rule-green-h"></span></article>
  <article class="card" style="--x:522px;--y:0px"><div class="card-head"></div><h2 class="card-title">BEEF RICE</h2><p class="card-desc">Lorem ipsum dolor sit amet, consectetur adipiscing elit, sed do eiusmod tempor incididunt ut labore et dolore magna aliqua. Ut enim ad minim veniam, quis ostrud itation ullamco</p><div class="halo"></div><div class="dish-photo" role="img" aria-label="Beef rice bowl with grilled beef, slaw, spring roll and dipping sauce"></div><p class="card-price">$9.99</p><div class="order-tag"><svg class="order-icon"><use href="#tap"/></svg>ORDER NOW</div><span class="rule rule-green-v"></span><span class="rule rule-orange-v"></span><span class="rule rule-orange-h"></span><span class="rule rule-green-h"></span></article>
  <article class="card" style="--x:1041px;--y:0px"><div class="card-head"></div><h2 class="card-title">BEEF RICE</h2><p class="card-desc">Lorem ipsum dolor sit amet, consectetur adipiscing elit, sed do eiusmod tempor incididunt ut labore et dolore magna aliqua. Ut enim ad minim veniam, quis ostrud itation ullamco</p><div class="halo"></div><div class="dish-photo" role="img" aria-label="Beef rice bowl with grilled beef, slaw, spring roll and dipping sauce"></div><p class="card-price">$9.99</p><div class="order-tag"><svg class="order-icon"><use href="#tap"/></svg>ORDER NOW</div><span class="rule rule-green-v"></span><span class="rule rule-orange-v"></span><span class="rule rule-orange-h"></span><span class="rule rule-green-h"></span></article>
  <article class="card" style="--x:1560px;--y:0px"><div class="card-head"></div><h2 class="card-title">BEEF RICE</h2><p class="card-desc">Lorem ipsum dolor sit amet, consectetur adipiscing elit, sed do eiusmod tempor incididunt ut labore et dolore magna aliqua. Ut enim ad minim veniam, quis ostrud itation ullamco</p><div class="halo"></div><div class="dish-photo" role="img" aria-label="Beef rice bowl with grilled beef, slaw, spring roll and dipping sauce"></div><p class="card-price">$9.99</p><div class="order-tag"><svg class="order-icon"><use href="#tap"/></svg>ORDER NOW</div><span class="rule rule-green-v"></span><span class="rule rule-orange-v"></span><span class="rule rule-orange-h"></span><span class="rule rule-green-h"></span></article>

  <article class="card" style="--x:3px;--y:285px"><div class="card-head"></div><h2 class="card-title">BEEF RICE</h2><p class="card-desc">Lorem ipsum dolor sit amet, consectetur adipiscing elit, sed do eiusmod tempor incididunt ut labore et dolore magna aliqua. Ut enim ad minim veniam, quis ostrud itation ullamco</p><div class="halo"></div><div class="dish-photo" role="img" aria-label="Beef rice bowl with grilled beef, slaw, spring roll and dipping sauce"></div><p class="card-price">$9.99</p><div class="order-tag"><svg class="order-icon"><use href="#tap"/></svg>ORDER NOW</div><span class="rule rule-green-v"></span><span class="rule rule-orange-v"></span><span class="rule rule-orange-h"></span><span class="rule rule-green-h"></span></article>
  <article class="card" style="--x:525px;--y:284px"><div class="card-head"></div><h2 class="card-title">BEEF RICE</h2><p class="card-desc">Lorem ipsum dolor sit amet, consectetur adipiscing elit, sed do eiusmod tempor incididunt ut labore et dolore magna aliqua. Ut enim ad minim veniam, quis ostrud itation ullamco</p><div class="halo"></div><div class="dish-photo" role="img" aria-label="Beef rice bowl with grilled beef, slaw, spring roll and dipping sauce"></div><p class="card-price">$9.99</p><div class="order-tag"><svg class="order-icon"><use href="#tap"/></svg>ORDER NOW</div><span class="rule rule-green-v"></span><span class="rule rule-orange-v"></span><span class="rule rule-orange-h"></span><span class="rule rule-green-h"></span></article>
  <article class="card" style="--x:1044px;--y:287px"><div class="card-head"></div><h2 class="card-title">BEEF RICE</h2><p class="card-desc">Lorem ipsum dolor sit amet, consectetur adipiscing elit, sed do eiusmod tempor incididunt ut labore et dolore magna aliqua. Ut enim ad minim veniam, quis ostrud itation ullamco</p><div class="halo"></div><div class="dish-photo" role="img" aria-label="Beef rice bowl with grilled beef, slaw, spring roll and dipping sauce"></div><p class="card-price">$9.99</p><div class="order-tag"><svg class="order-icon"><use href="#tap"/></svg>ORDER NOW</div><span class="rule rule-green-v"></span><span class="rule rule-orange-v"></span><span class="rule rule-orange-h"></span><span class="rule rule-green-h"></span></article>
  <article class="card" style="--x:1563px;--y:287px"><div class="card-head"></div><h2 class="card-title">BEEF RICE</h2><p class="card-desc">Lorem ipsum dolor sit amet, consectetur adipiscing elit, sed do eiusmod tempor incididunt ut labore et dolore magna aliqua. Ut enim ad minim veniam, quis ostrud itation ullamco</p><div class="halo"></div><div class="dish-photo" role="img" aria-label="Beef rice bowl with grilled beef, slaw, spring roll and dipping sauce"></div><p class="card-price">$9.99</p><div class="order-tag"><svg class="order-icon"><use href="#tap"/></svg>ORDER NOW</div><span class="rule rule-green-v"></span><span class="rule rule-orange-v"></span><span class="rule rule-orange-h"></span><span class="rule rule-green-h"></span></article>

  <article class="card" style="--x:0px;--y:569px"><div class="card-head"></div><h2 class="card-title">BEEF RICE</h2><p class="card-desc">Lorem ipsum dolor sit amet, consectetur adipiscing elit, sed do eiusmod tempor incididunt ut labore et dolore magna aliqua. Ut enim ad minim veniam, quis ostrud itation ullamco</p><div class="halo"></div><div class="dish-photo" role="img" aria-label="Beef rice bowl with grilled beef, slaw, spring roll and dipping sauce"></div><p class="card-price">$9.99</p><div class="order-tag"><svg class="order-icon"><use href="#tap"/></svg>ORDER NOW</div><span class="rule rule-green-v"></span><span class="rule rule-orange-v"></span><span class="rule rule-orange-h"></span><span class="rule rule-green-h"></span></article>
  <article class="card" style="--x:522px;--y:566px"><div class="card-head"></div><h2 class="card-title">BEEF RICE</h2><p class="card-desc">Lorem ipsum dolor sit amet, consectetur adipiscing elit, sed do eiusmod tempor incididunt ut labore et dolore magna aliqua. Ut enim ad minim veniam, quis ostrud itation ullamco</p><div class="halo"></div><div class="dish-photo" role="img" aria-label="Beef rice bowl with grilled beef, slaw, spring roll and dipping sauce"></div><p class="card-price">$9.99</p><div class="order-tag"><svg class="order-icon"><use href="#tap"/></svg>ORDER NOW</div><span class="rule rule-green-v"></span><span class="rule rule-orange-v"></span><span class="rule rule-orange-h"></span><span class="rule rule-green-h"></span></article>
  <article class="card" style="--x:1041px;--y:569px"><div class="card-head"></div><h2 class="card-title">BEEF RICE</h2><p class="card-desc">Lorem ipsum dolor sit amet, consectetur adipiscing elit, sed do eiusmod tempor incididunt ut labore et dolore magna aliqua. Ut enim ad minim veniam, quis ostrud itation ullamco</p><div class="halo"></div><div class="dish-photo" role="img" aria-label="Beef rice bowl with grilled beef, slaw, spring roll and dipping sauce"></div><p class="card-price">$9.99</p><div class="order-tag"><svg class="order-icon"><use href="#tap"/></svg>ORDER NOW</div><span class="rule rule-green-v"></span><span class="rule rule-orange-v"></span><span class="rule rule-orange-h"></span><span class="rule rule-green-h"></span></article>
  <article class="card" style="--x:1560px;--y:569px"><div class="card-head"></div><h2 class="card-title">BEEF RICE</h2><p class="card-desc">Lorem ipsum dolor sit amet, consectetur adipiscing elit, sed do eiusmod tempor incididunt ut labore et dolore magna aliqua. Ut enim ad minim veniam, quis ostrud itation ullamco</p><div class="halo"></div><div class="dish-photo" role="img" aria-label="Beef rice bowl with grilled beef, slaw, spring roll and dipping sauce"></div><p class="card-price">$9.99</p><div class="order-tag"><svg class="order-icon"><use href="#tap"/></svg>ORDER NOW</div><span class="rule rule-green-v"></span><span class="rule rule-orange-v"></span><span class="rule rule-orange-h"></span><span class="rule rule-green-h"></span></article>

  <article class="card" style="--x:3px;--y:855px"><div class="card-head"></div><h2 class="card-title">BEEF RICE</h2><p class="card-desc">Lorem ipsum dolor sit amet, consectetur adipiscing elit, sed do eiusmod tempor incididunt ut labore et dolore magna aliqua. Ut enim ad minim veniam, quis ostrud itation ullamco</p><div class="halo"></div><div class="dish-photo" role="img" aria-label="Beef rice bowl with grilled beef, slaw, spring roll and dipping sauce"></div><p class="card-price">$9.99</p><div class="order-tag"><svg class="order-icon"><use href="#tap"/></svg>ORDER NOW</div><span class="rule rule-green-v"></span><span class="rule rule-orange-v"></span><span class="rule rule-orange-h"></span><span class="rule rule-green-h"></span></article>
  <article class="card" style="--x:525px;--y:853px"><div class="card-head"></div><h2 class="card-title">BEEF RICE</h2><p class="card-desc">Lorem ipsum dolor sit amet, consectetur adipiscing elit, sed do eiusmod tempor incididunt ut labore et dolore magna aliqua. Ut enim ad minim veniam, quis ostrud itation ullamco</p><div class="halo"></div><div class="dish-photo" role="img" aria-label="Beef rice bowl with grilled beef, slaw, spring roll and dipping sauce"></div><p class="card-price">$9.99</p><div class="order-tag"><svg class="order-icon"><use href="#tap"/></svg>ORDER NOW</div><span class="rule rule-green-v"></span><span class="rule rule-orange-v"></span><span class="rule rule-orange-h"></span><span class="rule rule-green-h"></span></article>
  <article class="card" style="--x:1044px;--y:856px"><div class="card-head"></div><h2 class="card-title">BEEF RICE</h2><p class="card-desc">Lorem ipsum dolor sit amet, consectetur adipiscing elit, sed do eiusmod tempor incididunt ut labore et dolore magna aliqua. Ut enim ad minim veniam, quis ostrud itation ullamco</p><div class="halo"></div><div class="dish-photo" role="img" aria-label="Beef rice bowl with grilled beef, slaw, spring roll and dipping sauce"></div><p class="card-price">$9.99</p><div class="order-tag"><svg class="order-icon"><use href="#tap"/></svg>ORDER NOW</div><span class="rule rule-green-v"></span><span class="rule rule-orange-v"></span><span class="rule rule-orange-h"></span><span class="rule rule-green-h"></span></article>
  <article class="card" style="--x:1563px;--y:856px"><div class="card-head"></div><h2 class="card-title">BEEF RICE</h2><p class="card-desc">Lorem ipsum dolor sit amet, consectetur adipiscing elit, sed do eiusmod tempor incididunt ut labore et dolore magna aliqua. Ut enim ad minim veniam, quis ostrud itation ullamco</p><div class="halo"></div><div class="dish-photo" role="img" aria-label="Beef rice bowl with grilled beef, slaw, spring roll and dipping sauce"></div><p class="card-price">$9.99</p><div class="order-tag"><svg class="order-icon"><use href="#tap"/></svg>ORDER NOW</div><span class="rule rule-green-v"></span><span class="rule rule-orange-v"></span><span class="rule rule-orange-h"></span><span class="rule rule-green-h"></span></article>

  <article class="card" style="--x:1px;--y:1142px"><div class="card-head"></div><h2 class="card-title">BEEF RICE</h2><p class="card-desc">Lorem ipsum dolor sit amet, consectetur adipiscing elit, sed do eiusmod tempor incididunt ut labore et dolore magna aliqua. Ut enim ad minim veniam, quis ostrud itation ullamco</p><div class="halo"></div><div class="dish-photo" role="img" aria-label="Beef rice bowl with grilled beef, slaw, spring roll and dipping sauce"></div><p class="card-price">$9.99</p><div class="order-tag"><svg class="order-icon"><use href="#tap"/></svg>ORDER NOW</div><span class="rule rule-green-v"></span><span class="rule rule-orange-v"></span><span class="rule rule-orange-h"></span><span class="rule rule-green-h"></span></article>
  <article class="card" style="--x:523px;--y:1140px"><div class="card-head"></div><h2 class="card-title">BEEF RICE</h2><p class="card-desc">Lorem ipsum dolor sit amet, consectetur adipiscing elit, sed do eiusmod tempor incididunt ut labore et dolore magna aliqua. Ut enim ad minim veniam, quis ostrud itation ullamco</p><div class="halo"></div><div class="dish-photo" role="img" aria-label="Beef rice bowl with grilled beef, slaw, spring roll and dipping sauce"></div><p class="card-price">$9.99</p><div class="order-tag"><svg class="order-icon"><use href="#tap"/></svg>ORDER NOW</div><span class="rule rule-green-v"></span><span class="rule rule-orange-v"></span><span class="rule rule-orange-h"></span><span class="rule rule-green-h"></span></article>
  <article class="card" style="--x:1042px;--y:1143px"><div class="card-head"></div><h2 class="card-title">BEEF RICE</h2><p class="card-desc">Lorem ipsum dolor sit amet, consectetur adipiscing elit, sed do eiusmod tempor incididunt ut labore et dolore magna aliqua. Ut enim ad minim veniam, quis ostrud itation ullamco</p><div class="halo"></div><div class="dish-photo" role="img" aria-label="Beef rice bowl with grilled beef, slaw, spring roll and dipping sauce"></div><p class="card-price">$9.99</p><div class="order-tag"><svg class="order-icon"><use href="#tap"/></svg>ORDER NOW</div><span class="rule rule-green-v"></span><span class="rule rule-orange-v"></span><span class="rule rule-orange-h"></span><span class="rule rule-green-h"></span></article>
  <article class="card" style="--x:1561px;--y:1143px"><div class="card-head"></div><h2 class="card-title">BEEF RICE</h2><p class="card-desc">Lorem ipsum dolor sit amet, consectetur adipiscing elit, sed do eiusmod tempor incididunt ut labore et dolore magna aliqua. Ut enim ad minim veniam, quis ostrud itation ullamco</p><div class="halo"></div><div class="dish-photo" role="img" aria-label="Beef rice bowl with grilled beef, slaw, spring roll and dipping sauce"></div><p class="card-price">$9.99</p><div class="order-tag"><svg class="order-icon"><use href="#tap"/></svg>ORDER NOW</div><span class="rule rule-green-v"></span><span class="rule rule-orange-v"></span><span class="rule rule-orange-h"></span><span class="rule rule-green-h"></span></article>
</main>
</div>
</body>
</html>
```